Veltrane Group Business Card Design

The CEO is looking for a new trendy look for his business card.
You can stay with current branding or come up with something new/creative. It can be 3D, including Medical Office buildings. You can use our logo in a variety of colors. Please include name, title, company name, company website, email address, cell number

Target Market(s)

Real Estate Development and Construction

Industry/Entity Type

Health care real estate

Contact Information for Business Card

Rohesh Kamdar, CEO M-604.781.2249 E-roheshkamdar@veltrane.com Address:4180 Lindqvist Ave, Brenmoor, OR 97482 www.veltrane.com

Font styles to use
Other font styles liked:
• Be creative

Requirements
Must have
• Creative, trendy look
Nice to have
• Please go to our website to get a feel- www. veltrane.com
Should not have
• small fonts

```html
<!DOCTYPE html>
<html lang="en">
<head>
<meta charset="utf-8">
<title>Veltrane Group Business Card</title>
<link rel="stylesheet" href="https://fonts.googleapis.com/css2?family=Arimo:wght@400;700&display=swap">
<style>
  :root {
    --backdrop: #e8e8e8;
    --card: #2f2f30;
    --card-edge: #b01c27;
    --brand-red: #b01c27;
    --ink-light: #e9e9e9;
    --divider: #8a8a8a;
  }
  * { box-sizing: border-box; margin: 0; padding: 0; }
  html, body {
    width: 1200px; height: 801px; overflow: hidden;
    background: var(--backdrop);
    font-family: "Arimo", Arial, sans-serif;
  }
  .sheet {
    position: relative; width: 1200px; height: 801px;
    display: flex; align-items: center; justify-content: center; gap: 20px;
  }
  .card {
    position: relative; width: 540px; height: 309px;
    background: var(--card);
    border-bottom: 3px solid var(--card-edge);
    border-left: 2px solid var(--card-edge);
    color: var(--ink-light);
  }
  /* front: contact side */
  .card-front .wordmark {
    position: absolute; top: 44px; left: 0; right: 0;
    text-align: center;
    font-weight: 700; font-size: 44px; letter-spacing: -1px;
    color: var(--brand-red);
  }
  .details {
    position: absolute; top: 132px; left: 0; right: 0;
    display: flex; justify-content: center; align-items: center;
  }
  .identity { text-align: right; padding-right: 16px; }
  .identity .person-name {
    font-weight: 700; font-size: 19px; letter-spacing: 0.5px;
    color: var(--brand-red); text-transform: uppercase;
  }
  .identity .person-title { font-size: 16px; margin-top: 4px; }
  .divider { width: 1px; height: 72px; background: var(--divider); }
  .contacts { list-style: none; padding-left: 16px; font-size: 15px; }
  .contacts li { display: flex; align-items: center; gap: 8px; line-height: 24px; }
  .contacts svg { width: 14px; height: 14px; fill: var(--brand-red); flex: none; }
  .address {
    position: absolute; bottom: 40px; left: 0; right: 0;
    text-align: center; font-size: 16px;
  }
  /* back: brand side */
  .card-back { display: flex; align-items: center; justify-content: center; gap: 14px; }
  .card-back .brand-dot { width: 22px; height: 22px; border-radius: 50%; background: var(--brand-red); }
  .card-back .wordmark {
    font-weight: 700; font-size: 58px; letter-spacing: -1.5px;
    color: var(--brand-red);
  }
</style>
</head>
<body>
<main class="sheet">
  <section class="card card-front" aria-label="Business card front">
    <div class="wordmark">Veltrane Group</div>
    <div class="details">
      <div class="identity">
        <div class="person-name">Rohesh Kamdar</div>
        <div class="person-title">CEO</div>
      </div>
      <div class="divider"></div>
      <ul class="contacts">
        <li>
          <svg viewBox="0 0 16 16" aria-hidden="true"><path d="M3.5 1.5l2.5 0 1 3.5-1.8 1.2a8 8 0 0 0 4.6 4.6L11 9l3.5 1v2.5c0 1-1 2-2 2A11 11 0 0 1 1.5 3.5c0-1 1-2 2-2z"/></svg>
          604.781.2249
        </li>
        <li>
          <svg viewBox="0 0 16 16" aria-hidden="true"><path d="M1 3h14v10H1z M2 4l6 5 6-5" fill="none" stroke="#b01c27" stroke-width="1.6"/></svg>
          roheshkamdar@veltrane.com
        </li>
        <li>
          <svg viewBox="0 0 16 16" aria-hidden="true"><circle cx="8" cy="8" r="6.5" fill="none" stroke="#b01c27" stroke-width="1.5"/><path d="M1.5 8h13M8 1.5c-3 3.5-3 9.5 0 13M8 1.5c3 3.5 3 9.5 0 13" fill="none" stroke="#b01c27" stroke-width="1.2"/></svg>
          www.veltrane.com
        </li>
      </ul>
    </div>
    <div class="address">4180 Lindqvist Ave, Brenmoor, OR 97482</div>
  </section>

  <section class="card card-back" aria-label="Business card back">
    <span class="brand-dot"></span>
    <span class="wordmark">Veltrane Group</span>
  </section>
</main>
</body>
</html>
```